Updated business card

I would like to change the picture on the existing design. Please use the attached photo. Remove my last name from the logo and have that appear (just my first name with the lock symbol [trademarked]) appear horizontally or vertically? on the front of the card. My company information has changed on the back of the card. It should be "Harborline" instead of "Bramblegate 47 Juniper Homes", 2750 Fenwick Blvd. Arlington, VA 22207 is the new address. The Bramblegate 47 Juniper logo should be replaced with the Harborline logo which is attached as well. I am using Pix cards with the rounded edges for printing so the size is larger than the typically business card. The colors should remain consistent with what I have but can be used differently.

```html
<!DOCTYPE html>
<html lang="en">
<head>
<meta charset="utf-8">
<title>Rosalind Ashby — Business Card</title>
<link href="https://fonts.googleapis.com/css2?family=Lato:wght@400;700&family=Cormorant+Garamond:ital,wght@1,500&display=swap" rel="stylesheet">
<style>
  :root {
    --backdrop: #ece9e7;
    --card-grey: #bcbbc0;
    --card-white: #ffffff;
    --band-dark: #202326;
    --brand-pink: #d8178a;
    --ink: #1d1d1f;
    --rule: #555555;
    --watermark: #f1f1f3;
    --photo-warm: #a5603a;
    --photo-light: #d9d2cd;
  }
  * { box-sizing: border-box; margin: 0; padding: 0; }
  html, body { width: 1200px; height: 900px; overflow: hidden; }
  body {
    background: var(--backdrop);
    font-family: "Lato", Arial, sans-serif;
    color: var(--ink);
    position: relative;
  }
  .card { position: absolute; border-radius: 14px; overflow: hidden; }

  /* Front */
  .card-front {
    left: 78px; top: 34px; width: 587px; height: 363px;
    background: var(--card-grey);
  }
  .portrait {
    position: absolute; left: 0; top: 0; width: 315px; height: 363px;
    background: linear-gradient(160deg, var(--photo-light) 0%, #c9a48c 45%, var(--photo-warm) 100%);
  }
  .front-band {
    position: absolute; left: 315px; bottom: 0; width: 272px; height: 57px;
    background: var(--band-dark);
  }
  .front-name {
    position: absolute; left: 315px; top: 134px; width: 272px; text-align: center;
    font-weight: 400; text-transform: uppercase; line-height: 1;
    font-size: 40px; letter-spacing: 2px; color: var(--brand-pink);
  }
  .tagline {
    position: absolute; left: 315px; top: 212px; width: 272px; text-align: center;
    font-family: "Cormorant Garamond", Georgia, serif; font-style: italic; font-weight: 500;
    font-size: 26px; color: var(--ink); word-spacing: 4px; line-height: 1.2;
  }

  /* Back */
  .card-back {
    left: 388px; top: 506px; width: 565px; height: 350px;
    background: var(--card-white);
  }
  .watermark {
    position: absolute; left: 109px; top: 0; width: 350px; height: 350px;
    border-radius: 50%; background: var(--watermark);
  }
  .back-content { position: absolute; left: 0; top: 0; width: 100%; height: 100%; }
  .back-line {
    position: absolute; left: 0; width: 100%; text-align: center;
    font-size: 16px; line-height: 1; white-space: nowrap;
  }
  .agent-name { top: 40px; color: var(--brand-pink); font-size: 19px; font-weight: 700; letter-spacing: 0.3px; }
  .agent-role {
    top: 64px; font-family: "Cormorant Garamond", Georgia, serif;
    font-style: italic; font-size: 16px;
  }
  .agent-credential { top: 86px; }
  .phone { top: 145px; }
  .website { top: 168px; }
  .email { top: 191px; }
  .brokerage-address { top: 246px; }
  .divider {
    position: absolute; left: 173px; width: 222px; height: 16px;
    display: flex; align-items: center; justify-content: center; gap: 6px;
  }
  .divider::before, .divider::after { content: ""; flex: 1; height: 1px; background: var(--rule); }
  .divider-contact { top: 121px; }
  .divider-brokerage { top: 225px; font-weight: 700; font-size: 16px; }
  .contact-icons { display: flex; gap: 3px; }
  .contact-icons svg { width: 15px; height: 15px; display: block; }
  .brokerage-logo {
    position: absolute; right: 223px; top: 288px;
    font-size: 26px; font-weight: 400; letter-spacing: 2px; color: var(--ink);
    line-height: 1; white-space: nowrap;
  }
  .housing-badge {
    position: absolute; left: 350px; top: 266px; width: 56px; height: 56px;
    background: var(--ink); border-radius: 3px;
  }
</style>
</head>
<body>
  <section class="card card-front">
    <div class="portrait" role="img" aria-label="Portrait photo of the realtor"></div>
    <div class="front-band"></div>
    <div class="front-name">Rosalind</div>
    <div class="tagline">Real Estate Reimagined</div>
  </section>

  <section class="card card-back">
    <div class="watermark"></div>
    <div class="back-content">
      <div class="back-line agent-name">ROSALIND ASHBY,J.D.,LL.M.</div>
      <div class="back-line agent-role">Realtor</div>
      <div class="back-line agent-credential">Accredited Staging Professional</div>
      <div class="divider divider-contact">
        <span class="contact-icons">
          <svg viewBox="0 0 16 16"><circle cx="8" cy="8" r="8" fill="#d8178a"/><path d="M5 4.5l1.5-.5 1 2-1 .8a5 5 0 0 0 2.7 2.7l.8-1 2 1-.5 1.5c-3.5 0-6.5-3-6.5-6.5z" fill="#fff"/></svg>
          <svg viewBox="0 0 16 16"><circle cx="8" cy="8" r="8" fill="#d8178a"/><circle cx="8" cy="8" r="4" fill="none" stroke="#fff" stroke-width="1.3"/><path d="M4 8h8M8 4v8" stroke="#fff" stroke-width="1"/></svg>
          <svg viewBox="0 0 16 16"><circle cx="8" cy="8" r="8" fill="#d8178a"/><rect x="4" y="5" width="8" height="6" fill="#fff"/><path d="M4 5l4 3 4-3" fill="none" stroke="#d8178a" stroke-width="1"/></svg>
        </span>
      </div>
      <div class="back-line phone">202.555.0143</div>
      <div class="back-line website">Rosalind Ashby.com</div>
      <div class="back-line email">Rosalind@RosalindAshby.com</div>
      <div class="divider divider-brokerage"><span>HARBORLINE</span></div>
      <div class="back-line brokerage-address">2750 Fenwick Blvd. Arlington, VA 22207</div>
      <div class="brokerage-logo">HARBORLINE</div>
      <div class="housing-badge" role="img" aria-label="Housing badge"></div>
    </div>
  </section>
</body>
</html>
```